Modern Business Card for Larkwell 2018

Our company assumes the best about people. We are creating an online community of entrepreneurs and business leaders who struggle with marketing their business online.

This business card should POP! We recently got a new logo and are launching a new website next month, so our business cards should make a statement that feels:
-Fresh
-Smart
-Trustworthy
-Fun

Target Market(s)

small business owners, entrepreneurs

Industry/Entity Type

Digital Marketing

Contact Information for Business Card

Dimensions: 3.5" x 2"

Font styles to use
Sans Serif

Colors
f37122
ffffff

Requirements
Must have
• We need a business card with a modern, bold design. We will use one side of the card as a lead-generation offer, so text on one side will need to fit up to 140 characters. The business card should stick to our core colors (orange, black, and white).
Nice to have
• We think a vertical "portrait" design could be interesting.
Should not have
• Should not look like a traditional business card. The round icon should stand out from a distance.

```html
<!DOCTYPE html>
<html lang="en">
<head>
<meta charset="utf-8">
<title>Larkwell Business Card</title>
<link rel="stylesheet" href="https://fonts.googleapis.com/css2?family=Montserrat:wght@400;600;800&display=swap">
<style>
  :root{
    --orange:#f37122;
    --white:#ffffff;
    --ink:#1d1d1d;
    --paper:#f4f4f2;
    --backdrop:#e7e3de;
    --note:#ecebe6;
    --rule:#6f6f6f;
  }
  *{box-sizing:border-box;margin:0;padding:0}
  html,body{width:1200px;height:911px;overflow:hidden}
  body{background:var(--backdrop);font-family:"Montserrat",Arial,sans-serif;position:relative}
  .card{position:absolute;top:140px;width:360px;height:630px;overflow:hidden;border-radius:3px;box-shadow:0 10px 30px rgba(0,0,0,.18)}
  .card--front{left:200px;background:var(--paper)}
  .card--back{left:640px;background:var(--orange);color:var(--white)}

  .brand{position:absolute;top:150px;left:0;right:0;text-align:center}
  .brand__dot{width:34px;height:34px;border-radius:50%;background:var(--orange);margin:0 auto 12px}
  .brand__name{font-weight:800;font-size:44px;letter-spacing:1px;color:var(--ink);line-height:1}
  .brand__tagline{margin-top:8px;font-size:11px;font-weight:600;letter-spacing:1.5px;text-transform:uppercase;color:var(--ink)}

  .contact-band{position:absolute;left:-120px;top:440px;width:640px;height:640px;border-radius:50%;background:var(--orange)}
  .contact{position:absolute;right:26px;bottom:60px;text-align:right;color:var(--white);text-transform:uppercase}
  .contact__name{font-weight:800;font-size:26px;letter-spacing:.5px}
  .contact__title{font-weight:800;font-size:17px;letter-spacing:1px;margin-top:2px}
  .contact__email{font-weight:400;font-size:15px;letter-spacing:.5px;margin-top:4px}

  .offer__icon{position:absolute;top:46px;left:40px;width:110px;height:110px;border-radius:50%;background:var(--white)}
  .offer__headline{position:absolute;top:180px;left:40px;right:24px;font-weight:800;font-size:21px;line-height:1.15;text-transform:uppercase}
  .offer__line{display:block;white-space:nowrap}
  .offer__body{position:absolute;top:268px;left:40px;right:28px;font-size:14px;line-height:1.3;text-transform:uppercase;font-weight:400}
  .offer__body strong{font-weight:800}
  .offer__url{display:inline-block;margin-top:10px;background:var(--ink);color:var(--orange);font-weight:800;font-size:16px;padding:5px 16px;border-radius:20px;text-transform:none;border:2px solid #555}
  .notes{position:absolute;left:22px;right:22px;bottom:26px;height:210px;background:linear-gradient(100deg,#f6f5f1,var(--note) 50%,#d9d8d2);padding:18px 24px}
  .notes__line{height:28px;border-bottom:1px dotted var(--rule)}
</style>
</head>
<body>
  <section class="card card--front" aria-label="Card front">
    <div class="brand">
      <div class="brand__dot"></div>
      <div class="brand__name">LARKWELL</div>
      <div class="brand__tagline">Craft tales that move people to act</div>
    </div>
    <div class="contact-band"></div>
    <div class="contact">
      <div class="contact__name">Dana Whitfield</div>
      <div class="contact__title">Story Marketing Coach</div>
      <div class="contact__email">dana@larkwellnow.com</div>
    </div>
  </section>

  <section class="card card--back" aria-label="Card back">
    <div class="offer__icon"></div>
    <h1 class="offer__headline">
      <span class="offer__line">Find more clients.</span>
      <span class="offer__line">Earn more trust.</span>
      <span class="offer__line">Build a bigger reach.</span>
    </h1>
    <p class="offer__body">Claim your free <strong>Larkwell</strong> starter kit and our online growth guide now at<br><span class="offer__url">Larkwellnow.com/start</span></p>
    <div class="notes">
      <div class="notes__line"></div>
      <div class="notes__line"></div>
      <div class="notes__line"></div>
      <div class="notes__line"></div>
      <div class="notes__line"></div>
      <div class="notes__line"></div>
    </div>
  </section>
</body>
</html>
```